Puffy Clouds Cotton Candy

Looking for a logo design and business cards to help a 13 year old entrepreneur promote her cotton candy business.
Contact Information for Business Card
Name, Phone & Email
Colors
E54698
E96AAD
F1A4CE
F9D9EA
FCEFF6
A7469A
B969AE
D3A5CF
EDDBEB
F8F0F9
6B429C
8869AF
B7A5CE
E3DAEB
F3F0F8
Requirements
Must have
- A fun feel that is appropriate for a teenage girl selling cotton candy

```html
<!DOCTYPE html>
<html lang="en">
<head>
<meta charset="utf-8">
<title>Puffy Clouds Cotton Candy – Business Card</title>
<link href="https://fonts.googleapis.com/css2?family=Poppins:wght@400;500;600;700&display=swap" rel="stylesheet">
<style>
  :root {
    --pink: #E54698;
    --pink-soft: #F9D9EA;
    --purple: #6B429C;
    --white: #FFFFFF;
    --stage: #F3F0F8;
    --font: "Poppins", sans-serif;
  }
  * { box-sizing: border-box; margin: 0; padding: 0; }
  html, body {
    width: 1200px; height: 900px; overflow: hidden;
    background: var(--stage);
    font-family: var(--font);
  }
  .sheet {
    width: 1200px; height: 900px;
    display: flex; flex-direction: column;
    align-items: center; justify-content: center; gap: 40px;
  }
  .card {
    position: relative;
    width: 700px; height: 400px;
    overflow: hidden;
    box-shadow: 0 6px 18px rgba(107, 66, 156, 0.18);
  }

  /* Back side */
  .card--back {
    background: var(--pink);
    display: flex; flex-direction: column;
    align-items: center; justify-content: center; gap: 22px;
  }
  .brand-dot {
    width: 120px; height: 120px; border-radius: 50%;
    border: 6px solid var(--white);
  }
  .brand-name {
    font-weight: 700; font-size: 38px; line-height: 1.1;
    text-align: center; color: var(--white);
  }

  /* Front side */
  .card--front { background: var(--white); }
  .wave { position: absolute; inset: 0; width: 100%; height: 100%; }
  .person { position: absolute; left: 56px; top: 50px; }
  .person__name { font-weight: 600; font-size: 30px; color: var(--pink); line-height: 1.1; }
  .person__role { font-weight: 400; font-size: 18px; color: var(--purple); }
  .contact {
    position: absolute; left: 72px; top: 150px;
    list-style: none; color: var(--purple); font-size: 18px; line-height: 1.45;
  }
  .contact__item { display: flex; align-items: center; gap: 10px; }
  .contact__icon { width: 20px; height: 20px; flex: none; }
  .contact__address { margin-top: 12px; padding-left: 30px; }
  .front-brand {
    position: absolute; right: 44px; top: 28px; width: 230px;
    display: flex; flex-direction: column; align-items: center; gap: 12px;
  }
  .front-brand .brand-dot { width: 84px; height: 84px; border-color: var(--pink); border-width: 5px; }
  .front-brand .brand-name { color: var(--pink); font-size: 26px; }
  .website {
    position: absolute; right: 40px; bottom: 46px;
    color: var(--white); font-size: 17px; font-weight: 500;
  }
</style>
</head>
<body>
<main class="sheet">
  <section class="card card--back" aria-label="Card back">
    <div class="brand-dot"></div>
    <p class="brand-name">Puffy Clouds<br>Cotton Candy</p>
  </section>

  <section class="card card--front" aria-label="Card front">
    <svg class="wave" viewBox="0 0 700 400" preserveAspectRatio="none" aria-hidden="true">
      <path d="M0 336 C 180 344, 300 312, 410 252 C 428 242, 444 232, 460 224 C 340 314, 180 330, 0 322 Z" fill="var(--purple)"/>
      <path d="M0 352 C 200 356, 360 318, 480 258 C 560 220, 620 206, 700 200 L700 400 L0 400 Z" fill="var(--pink)"/>
    </svg>

    <div class="person">
      <p class="person__name">Maya Ellison</p>
      <p class="person__role">Managing Director</p>
    </div>

    <ul class="contact">
      <li class="contact__item">
        <svg class="contact__icon" viewBox="0 0 24 24" aria-hidden="true"><path d="M6.6 10.8a15 15 0 0 0 6.6 6.6l2.2-2.2a1 1 0 0 1 1-.25 11.4 11.4 0 0 0 3.6.6 1 1 0 0 1 1 1V20a1 1 0 0 1-1 1A17 17 0 0 1 3 4a1 1 0 0 1 1-1h3.5a1 1 0 0 1 1 1c0 1.25.2 2.45.6 3.6a1 1 0 0 1-.25 1z" fill="var(--pink)"/></svg>
        055-318 720 446
      </li>
      <li class="contact__item">
        <svg class="contact__icon" viewBox="0 0 24 24" aria-hidden="true"><rect x="2" y="5" width="20" height="14" rx="1" fill="var(--pink)"/><path d="M2.5 6l9.5 7 9.5-7" fill="none" stroke="var(--white)" stroke-width="1.6"/></svg>
        hello@puffyclouds.com
      </li>
      <li class="contact__address">88 Meadow Lane<br>Brookfield, 20417</li>
    </ul>

    <div class="front-brand">
      <div class="brand-dot"></div>
      <p class="brand-name">Puffy Clouds<br>Cotton Candy</p>
    </div>

    <p class="website">www.puffyclouds.com</p>
  </section>
</main>
</body>
</html>
```